Hearthside Lending Relief

Please help us give our website a remake or a FACELIFT. It is not very good but it says what we need it to say. But the design is terrible.
I would like our new design font and logo to be used as the theme.

I also want more photos on the site.

I also want consistency with the pages so they look clean.

We want the professionals to do this, let's see what you got!

Thank you!
Updates

Project Deadline Extended
Reason: I can understand you want to be paid. So I will commit to the fee but I want you to have time to make a KICK ASS website for me dudes! Thanks

HI!  Just wanted to say thanks for your time on these.  A lot are great.  However the firefighters have nothing to do with Foreclosure.  We are saving peoples homes from the bank taking them and selling them.   I LOVE the house photos and the families on the website.  That is the direction we like.  THanks.

THANK U ALL FOR THE WORK!   I like a few ending in the numbers: 147  733  693  536  620  478  727  508     I will go over them and choose one soon.  Thank you.   You will be paid shortly. 

Requirements
Must have
• Bright, Upbeat photos. Color scheme should be in order. We like icons on the bottom. not just text.

```html
<!DOCTYPE html>
<html lang="en">
<head>
<meta charset="utf-8">
<title>Hearthside Lending Relief</title>
<link href="https://fonts.googleapis.com/css2?family=Open+Sans:ital,wght@0,400;0,600;0,700;1,400&display=swap" rel="stylesheet">
<style>
:root{
  --red:#d0202e;
  --ink:#4a4a4a;
  --muted:#6b6b6b;
  --page:#f2f2f2;
  --darker:#2e2e2e;
  --footer:#444444;
  --footer-text:#d8d8d8;
  --field:#e6e6e6;
  --field-line:#c9c9c9;
  --white:#ffffff;
}
*{margin:0;padding:0;box-sizing:border-box}
html,body{width:900px;height:1200px;overflow:hidden}
body{font-family:"Open Sans",Arial,sans-serif;background:var(--page);color:var(--ink);position:relative;font-size:10px;letter-spacing:-0.1px}
.site-header{position:absolute;left:0;top:0;width:900px;height:95px;background:linear-gradient(#f7f7f7,#ececec);border-bottom:1px solid #d6d6d6}
.brand{position:absolute;left:101px;top:22px;display:flex;align-items:center;gap:10px}
.brand-mark{width:46px;height:46px;border-radius:50%;background:var(--red)}
.brand-name{color:var(--red);font-weight:700;font-size:17px;line-height:17px;width:170px;text-transform:uppercase;letter-spacing:0}
.callout{position:absolute;right:96px;top:28px;text-align:left;letter-spacing:0}
.callout-label{font-size:11px;color:var(--muted);font-weight:600}
.callout-phone{font-size:25px;color:var(--red);font-weight:600;line-height:28px}
.main-nav{position:absolute;left:97px;top:106px;width:706px;height:35px;background:linear-gradient(#505050,#2c2c2c);border-radius:3px;display:flex}
.main-nav a{color:var(--white);text-decoration:none;font-size:11.5px;letter-spacing:0;display:flex;align-items:center;justify-content:center;border-right:1px solid #5a5a5a}
.main-nav a:last-child{border-right:0}
.slider{position:absolute;left:97px;top:151px;width:706px;height:283px;background:var(--white);border:1px solid #d8d8d8;border-radius:3px;padding:4px}
.slide-photo{width:100%;height:100%;background:linear-gradient(180deg,#b9bcc1 0%,#9a8f87 35%,#8c5a42 60%,#5d4a3e 100%)}
.slider-dots{position:absolute;left:21px;bottom:12px;display:flex;gap:6px}
.slider-dots span{width:17px;height:17px;border-radius:50%;background:rgba(255,255,255,.45)}
.slider-dots span.is-active{background:var(--white)}
h2{font-weight:400;color:var(--red);font-size:18.5px;line-height:24px;letter-spacing:0}
.btn{display:inline-block;background:var(--darker);color:var(--white);border-radius:4px;font-size:12px;letter-spacing:0;padding:6px 15px}
.welcome{position:absolute;left:99px;top:466px;width:456px}
.welcome h2{margin-bottom:5px}
.welcome p{line-height:17.3px;margin-bottom:5px}
.welcome .btn{margin-top:17px;margin-left:-1px}
.services{position:absolute;left:589px;top:466px;width:214px}
.services h2{margin-bottom:5px}
.services .intro{line-height:17.3px}
.services ul{list-style:none;margin-top:9px}
.services li{position:relative;padding-left:19px;line-height:13px;margin-bottom:12.5px}
.services li svg{position:absolute;left:0;top:2px}
.services .btn-row{text-align:right;margin-top:18px}
.testimonials{position:absolute;left:99px;top:774px;width:333px}
.testimonials h2{margin-bottom:5px}
.quote{font-style:italic;line-height:17.3px}
.quote-mark{font-style:normal;font-weight:700;font-size:24px;color:#8a8a8a;line-height:0;vertical-align:-7px;margin-right:4px}
.quote-author{text-align:right;color:var(--red);font-weight:600;margin-top:6px;font-size:10px}
.quote-author.first{margin-bottom:28px}
.quick-contact{position:absolute;left:529px;top:774px;width:276px}
.quick-contact h2{margin-bottom:14px}
.field-row{display:flex;justify-content:space-between;margin-bottom:13px}
.field{width:131px;height:22px;background:var(--field);border:1px solid var(--field-line);border-radius:3px;font-style:italic;color:#8d8d8d;font-size:10px;padding:4px 8px}
.field-message{width:274px;height:96px}
.quick-contact .btn{position:absolute;right:0;top:222px;padding:6px 14px}
.site-footer{position:absolute;left:0;top:1064px;width:900px;height:136px;background:var(--footer);color:var(--footer-text);font-size:9.5px;letter-spacing:0}
.footer-col{position:absolute;top:12px}
.footer-col h3{color:var(--white);font-weight:600;font-size:13px;margin-bottom:6px}
.footer-col p{line-height:13.8px}
.footer-col li{line-height:16.4px;list-style:none}
.footer-col strong{color:var(--white);font-size:9.5px}
.connect li{display:flex;align-items:center;gap:8px;margin-bottom:4.5px}
.connect .icon{width:15px;height:15px;border-radius:50%;background:#d8d8d8}
.footer-brand{position:absolute;left:638px;top:16px;width:150px;height:46px;background:var(--white);display:flex;align-items:center;gap:6px;padding:0 6px}
.footer-brand .brand-mark{width:30px;height:30px;flex:none}
.footer-brand .brand-name{font-size:11px;line-height:11.5px;width:auto}
.legal{position:absolute;left:638px;top:75px;color:#a5a5a5;font-size:8.5px;line-height:15px}
</style>
</head>
<body>
<header class="site-header">
  <div class="brand">
    <div class="brand-mark"></div>
    <div class="brand-name">Hearthside Lending Relief</div>
  </div>
  <div class="callout">
    <div class="callout-label">CALL TOLL FREE NOW</div>
    <div class="callout-phone">877-555-0142</div>
  </div>
</header>

<nav class="main-nav">
  <a style="width:128px">Home</a>
  <a style="width:128px">About Us</a>
  <a style="width:123px">Services</a>
  <a style="width:173px">Finance Options</a>
  <a style="width:154px">Contact Us</a>
</nav>

<section class="slider">
  <div class="slide-photo" role="img" aria-label="Photo of a brick family house with a foreclosure sign in the front yard"></div>
  <div class="slider-dots"><span class="is-active"></span><span></span><span></span><span></span></div>
</section>

<section class="welcome">
  <h2>Welcome to Our Site</h2>
  <p>HEARTHSIDE LENDING RELIEF specializes in assisting homeowners who are in FORECLOSURE, by offering solid alternatives to losing your home in a Trustee Sale. Having your home foreclosed on can damage your credit for up to 7 years. Most foreclosures end with the home owner being evicted from their home, leaving them with no money, no place to live and without ample time to safely remove their possessions from their home. There is no need to have this happen to you. No matter what part of foreclosure process you are in, WE CAN HELP!</p>
  <p>If you have received a Notice of Default (NOD) or Notice of Trustee Sale (NTS), you have options. Contact us today to speak to one of our licensed specialist, and let us help you put this situation behind you. We speak to hundreds of homeowners every day, we understand how frustrating this can be. Don't live in fear of what is to come. You have other options, please call or email us today and we will immediately put our specialist to work finding you a solution.</p>
  <span class="btn">More</span>
</section>

<section class="services">
  <h2>Our Services</h2>
  <p class="intro">Some of the solutions our specialist can discuss with you are:</p>
  <ul>
    <li><svg width="9" height="9" viewBox="0 0 9 9"><circle cx="4.5" cy="4.5" r="4.5" fill="#8a8a8a"/><path d="M3.5 2.5 5.5 4.5 3.5 6.5" stroke="#fff" stroke-width="1.2" fill="none"/></svg>Bringing your mortgage current to stop the foreclosure.</li>
    <li><svg width="9" height="9" viewBox="0 0 9 9"><circle cx="4.5" cy="4.5" r="4.5" fill="#8a8a8a"/><path d="M3.5 2.5 5.5 4.5 3.5 6.5" stroke="#fff" stroke-width="1.2" fill="none"/></svg>HLR can purchase your home with CASH in 7-10 days.</li>
    <li><svg width="9" height="9" viewBox="0 0 9 9"><circle cx="4.5" cy="4.5" r="4.5" fill="#8a8a8a"/><path d="M3.5 2.5 5.5 4.5 3.5 6.5" stroke="#fff" stroke-width="1.2" fill="none"/></svg>Financing/Purchase Options.</li>
    <li><svg width="9" height="9" viewBox="0 0 9 9"><circle cx="4.5" cy="4.5" r="4.5" fill="#8a8a8a"/><path d="M3.5 2.5 5.5 4.5 3.5 6.5" stroke="#fff" stroke-width="1.2" fill="none"/></svg>Relocations Assistance - if needed.</li>
    <li><svg width="9" height="9" viewBox="0 0 9 9"><circle cx="4.5" cy="4.5" r="4.5" fill="#8a8a8a"/><path d="M3.5 2.5 5.5 4.5 3.5 6.5" stroke="#fff" stroke-width="1.2" fill="none"/></svg>Remodel your home to increase it's value.</li>
    <li><svg width="9" height="9" viewBox="0 0 9 9"><circle cx="4.5" cy="4.5" r="4.5" fill="#8a8a8a"/><path d="M3.5 2.5 5.5 4.5 3.5 6.5" stroke="#fff" stroke-width="1.2" fill="none"/></svg>Many other options are available.</li>
  </ul>
  <div class="btn-row"><span class="btn">More</span></div>
</section>

<section class="testimonials">
  <h2>Testimonials</h2>
  <p class="quote"><span class="quote-mark">&ldquo;</span>I'd like to express my gratitude to you and your company and I have to add, for all of the trustworthy and reliable service that you bring to the public. Your company helped put me back together, you in particular are awesome! Thank you again Theo.... "</p>
  <p class="quote-author first">Rosalind</p>
  <p class="quote"><span class="quote-mark">&ldquo;</span>Hearthside Lending Relief has been an absolute life saver for me and my family. Their services have changed everything. Instead of my house going into foreclosure and losing everything I own, I now have a chance to start over and the money to do it with! They've been fast, friendly and efficient. I would recommend their services to anyone facing foreclosure... "</p>
  <p class="quote-author">Dana W.</p>
</section>

<section class="quick-contact">
  <h2>Quick Contact Us</h2>
  <div class="field-row"><div class="field">First Name</div><div class="field">Last Name</div></div>
  <div class="field-row"><div class="field">Email Address</div><div class="field">Contact No.</div></div>
  <div class="field field-message">Type Message here...</div>
  <span class="btn">Click for Submit</span>
</section>

<footer class="site-footer">
  <div class="footer-col" style="left:98px">
    <h3>Contact Us</h3>
    <p><strong>HEARTHSIDE LENDING RELIEF</strong></p>
    <p>118 Harbor Lane, Suite 210</p>
    <p>Oceanview, CA 92000</p>
    <p>877-555-0142</p>
  </div>
  <div class="footer-col" style="left:319px">
    <h3>Company Info</h3>
    <ul><li>Home</li><li>About Us</li><li>Services</li><li>Financing Option</li><li>Contact Us</li></ul>
  </div>
  <div class="footer-col connect" style="left:497px">
    <h3>Connect Us</h3>
    <ul>
      <li><span class="icon"></span>Friendface</li>
      <li><span class="icon"></span>Chirper</li>
      <li><span class="icon"></span>Circles +</li>
      <li><span class="icon"></span>Rss Feed</li>
    </ul>
  </div>
  <div class="footer-brand">
    <div class="brand-mark"></div>
    <div class="brand-name">Hearthside Lending Relief</div>
  </div>
  <div class="legal">© 2012 Hearthside Lending Relief<br>All Right Reserved &nbsp;|&nbsp; Privacy Policy</div>
</footer>
</body>
</html>
```